We need a business card design for a new company located in Missouri City, TX, entitled 'BrightPath Chiropractic & Holistic Center'. Our services include restoration of health and vitality, spinal exam, health assessment, dietary & fitness programs, lymphatic & therapeutic massage, detox & remineralize body wraps, far infrared sauna therapy

Industry/Entity Type

Business

Contact Information for Business Card

BrightPath Chiropractic & Holistic Center, Marlene Okafor LMT, 4215 Elm Ridge Rd., Suite 310, Missouri City, TX 77482, 281-555-0193

```html
<!DOCTYPE html>
<html lang="en">
<head>
<meta charset="utf-8">
<title>BrightPath Chiropractic &amp; Holistic Center – Business Card</title>
<link href="https://fonts.googleapis.com/css2?family=Libre+Baskerville&family=Open+Sans:wght@400;600&family=Playfair+Display:wght@400;700&display=swap" rel="stylesheet">
<style>
  :root {
    --backdrop: #ece8e2;
    --card-white: #ffffff;
    --ink: #1c1c1c;
    --ink-soft: #3a3a3a;
    --blue: #2f79a8;
    --teal: #1fb3a3;
    --teal-deep: #179c90;
    --teal-light: #36c4b4;
    --icon-blue: #2a86b8;
  }
  * { box-sizing: border-box; margin: 0; padding: 0; }
  html, body { width: 1200px; height: 892px; overflow: hidden; }
  body {
    background: var(--backdrop);
    display: flex;
    flex-direction: column;
    align-items: center;
    justify-content: center;
    gap: 40px;
  }
  .card {
    width: 640px;
    height: 366px;
    position: relative;
    overflow: hidden;
    box-shadow: 0 6px 18px rgba(0,0,0,0.18);
  }

  /* Front */
  .card-front { background: var(--card-white); }
  .brand {
    position: absolute;
    left: 34px;
    top: 108px;
    width: 250px;
  }
  .brand-mark {
    width: 38px; height: 38px;
    border-radius: 50%;
    background: var(--teal);
    margin-bottom: 16px;
  }
  .brand-name {
    font-family: "Libre Baskerville", Georgia, serif;
    font-size: 30px;
    color: var(--ink);
    line-height: 1.1;
  }
  .brand-tagline {
    font-family: "Open Sans", Arial, sans-serif;
    font-size: 13px;
    color: var(--ink-soft);
    margin-top: 8px;
  }
  .contact-block {
    position: absolute;
    left: 318px;
    top: 40px;
    height: 230px;
    border-left: 2px solid var(--blue);
    padding-left: 16px;
  }
  .person-name {
    font-family: "Libre Baskerville", Georgia, serif;
    font-size: 27px;
    color: var(--blue);
  }
  .person-title {
    font-family: "Libre Baskerville", Georgia, serif;
    font-size: 14px;
    color: var(--ink-soft);
    margin-top: 2px;
  }
  .name-rule {
    position: absolute;
    left: 0; top: 72px;
    width: 290px;
    border-top: 1px solid var(--blue);
  }
  .contact-list {
    list-style: none;
    margin-top: 90px;
    font-family: "Open Sans", Arial, sans-serif;
    font-size: 15px;
    color: var(--ink);
  }
  .contact-list li {
    display: flex;
    align-items: center;
    gap: 9px;
    margin-bottom: 6px;
  }
  .contact-icon {
    width: 15px; height: 15px;
    background: var(--icon-blue);
    border-radius: 2px;
    flex: none;
  }
  .address-band {
    position: absolute;
    left: 0; right: 0; bottom: 0;
    height: 56px;
    background: var(--teal);
    color: #fff;
    font-family: "Open Sans", Arial, sans-serif;
    font-size: 14px;
    display: flex;
    align-items: center;
    padding-left: 34px;
  }

  /* Back */
  .card-back {
    background: linear-gradient(135deg, var(--teal-light) 0%, var(--teal) 50%, var(--teal-deep) 100%);
    padding: 26px 40px;
  }
  .services-title {
    font-family: "Playfair Display", Georgia, serif;
    font-weight: 700;
    font-size: 30px;
    color: var(--ink);
  }
  .services-rule {
    border-top: 1.5px solid var(--ink);
    width: 400px;
    margin: 6px 0 14px;
  }
  .services-list {
    list-style: none;
    font-family: "Playfair Display", Georgia, serif;
    font-size: 20px;
    line-height: 1.3;
    color: var(--ink);
  }
</style>
</head>
<body>
  <section class="card card-front">
    <div class="brand">
      <div class="brand-mark"></div>
      <div class="brand-name">BrightPath</div>
      <div class="brand-tagline">Chiropractic &amp; Holistic Center</div>
    </div>
    <div class="contact-block">
      <div class="person-name">Dana Whitfield</div>
      <div class="person-title">Chief Executive</div>
      <div class="name-rule"></div>
      <ul class="contact-list">
        <li>
          <svg class="contact-icon" viewBox="0 0 15 15"><rect width="15" height="15" rx="2" fill="#2a86b8"/><path d="M4 3.5l2 .3.6 2-1 .8a6 6 0 0 0 2.8 2.8l.8-1 2 .6.3 2c-4 .6-8-3.4-7.5-7.5z" fill="#fff"/></svg>
          281-555-0193
        </li>
        <li>
          <svg class="contact-icon" viewBox="0 0 15 15"><rect width="15" height="15" rx="2" fill="#2a86b8"/><rect x="3" y="4.5" width="9" height="6" fill="none" stroke="#fff" stroke-width="1.2"/><path d="M3 4.5l4.5 3.5 4.5-3.5" fill="none" stroke="#fff" stroke-width="1.2"/></svg>
          dana.whitfield@brightpathhc.com
        </li>
        <li>
          <svg class="contact-icon" viewBox="0 0 15 15"><rect width="15" height="15" rx="2" fill="#2a86b8"/><circle cx="7.5" cy="7.5" r="4" fill="none" stroke="#fff" stroke-width="1.2"/><path d="M3.5 7.5h8M7.5 3.5c-2 2.5-2 5.5 0 8M7.5 3.5c2 2.5 2 5.5 0 8" fill="none" stroke="#fff" stroke-width="1"/></svg>
          www.brightpathhc.com
        </li>
      </ul>
    </div>
    <div class="address-band">Marlene Okafor LMT, 4215 Elm Ridge Rd., Suite 310, Missouri City, TX 77482</div>
  </section>

  <section class="card card-back">
    <h2 class="services-title">Services</h2>
    <div class="services-rule"></div>
    <ul class="services-list">
      <li>Restoration of health and vitality</li>
      <li>Spinal exam</li>
      <li>Health assessment</li>
      <li>Dietary &amp; fitness programs</li>
      <li>Lymphatic &amp; therapeutic massage</li>
      <li>Detox &amp; remineralize body wraps</li>
      <li>Far infrared sauna therapy</li>
    </ul>
  </section>
</body>
</html>
```